Stationery Design Project

I need a stationary design for our company. we are based in Houston, TX and we are called Mira Vell Lending. And we are wanting to brand our MoneyMendPlus program, which includes our tax preparation and restoration, credit repair service. Although our business offers other programs, we are interested in mainly focusing on The MoneyMendPlus program. We are looking for way to brand our ourselves and I believe that a great stationery design will help in achieving this goal. Our logo design is blue and light blue. the slogan is orange.

Industry/Entity Type

Business

Requirements
Must have
• Address: 30871 Calloway Ln. B-22
Houston, TX 75419
Tel. 555-318-6207
Fax 555-294-7153
www.miravelllending.example
info@miravelllending.example
Our Slogan: Peace of Mind, Renewed!

```html
<!DOCTYPE html>
<html lang="en">
<head>
<meta charset="utf-8">
<title>Mira Vell Lending – MoneyMendPlus Business Cards</title>
<link href="https://fonts.googleapis.com/css2?family=Arimo:wght@400&family=Tinos:wght@400&display=swap" rel="stylesheet">
<style>
  :root {
    --bg: #ecebe7;
    --white: #ffffff;
    --brand-blue: #1f6fb8;
    --deep-blue: #0d4a92;
    --navy: #0f3a63;
    --sky: #8cc8ec;
    --pale-blue: #cfe3f5;
    --orange: #f39a1e;
    --swoosh-grey: #e4e7ea;
    --ink: #3a3f45;
  }
  * { margin: 0; padding: 0; box-sizing: border-box; }
  html, body { width: 1200px; height: 772px; overflow: hidden; background: var(--bg); }
  .sheet { position: relative; width: 1200px; height: 772px; }
  .card {
    position: absolute; width: 510px; height: 285px;
    border-radius: 16px; overflow: hidden;
  }
  .card--front { left: 85px; top: 85px; background: var(--white); }
  .card--back-blue { left: 630px; top: 85px; background: linear-gradient(90deg, var(--brand-blue), var(--deep-blue)); }
  .card--back-pale { left: 85px; top: 403px; background: var(--pale-blue); }
  .card--front-plain { left: 630px; top: 403px; background: var(--white); }

  .wave { position: absolute; inset: 0; width: 510px; height: 285px; }

  .program-name {
    position: absolute; font-family: "Tinos", serif; font-size: 34px; line-height: 40px;
    color: var(--brand-blue); white-space: nowrap; transform: translateX(-50%);
  }
  .slogan {
    position: absolute; font-family: "Tinos", serif; font-size: 16px; line-height: 20px;
    letter-spacing: 2px; color: var(--ink); white-space: nowrap; transform: translateX(-50%);
  }
  .web {
    position: absolute; left: 0; right: 0; text-align: center;
    font-family: "Arimo", sans-serif; font-size: 12px; line-height: 14px; letter-spacing: 4px;
  }
  .web--front { left: 361px; right: auto; transform: translateX(-50%); white-space: nowrap; letter-spacing: 1px; color: var(--ink); font-size: 11px; }
  .web--light { color: var(--white); }
  .web--dark { color: var(--deep-blue); }
  .web--ink { color: var(--ink); }

  .contact {
    position: absolute; left: 20px; top: 192px;
    font-family: "Arimo", sans-serif; font-size: 11.5px; line-height: 16px; color: var(--white);
  }
  .contact .address { margin-top: 14px; }

  .company-mark {
    position: absolute; left: 50%; top: 42px; width: 100px; height: 100px;
    margin-left: -50px; background: var(--navy); border: 3px solid var(--white);
    display: flex; align-items: flex-end; justify-content: center; padding-bottom: 12px;
  }
  .card--back-pale .company-mark { top: 46px; border-color: var(--navy); }
  .company-name {
    font-family: "Tinos", serif; font-size: 11px; color: var(--white);
    text-align: center; white-space: nowrap;
  }
</style>
</head>
<body>
<main class="sheet">

  <section class="card card--front" aria-label="Business card front">
    <svg class="wave" viewBox="0 0 510 285" aria-hidden="true">
      <path d="M0,112 C90,104 180,150 260,200 C330,240 430,258 510,258 L510,285 L0,285 Z" fill="var(--swoosh-grey)"/>
      <path d="M0,112 C90,104 180,150 260,200 C330,240 430,258 510,258" fill="none" stroke="var(--sky)" stroke-width="4"/>
      <path transform="translate(0,12)" d="M0,112 C90,104 180,150 260,200 C330,240 430,258 510,258" fill="none" stroke="var(--orange)" stroke-width="4"/>
      <path transform="translate(0,18)" d="M0,112 C90,104 180,150 260,200 C330,240 430,258 510,258 L510,285 L0,285 Z" fill="var(--brand-blue)"/>
    </svg>
    <div class="program-name" style="left:361px; top:84px;">MoneyMendPlus</div>
    <div class="slogan" style="left:361px; top:134px;">PEACE OF MIND, RENEWED!</div>
    <div class="web web--front" style="top:172px;">www.miravelllending.example</div>
    <div class="contact">
      <div>T: 555-318-6207</div>
      <div>F: 555-294-7153</div>
      <div>E: info@miravelllending.example</div>
      <div class="address">30871 Calloway Ln. B-22, Houston, TX 75419</div>
    </div>
  </section>

  <section class="card card--back-blue" aria-label="Business card back, blue">
    <div class="company-mark"><span class="company-name">Mira Vell Lending</span></div>
    <div class="web web--light" style="top:232px;">www.miravelllending.example</div>
  </section>

  <section class="card card--back-pale" aria-label="Business card back, pale blue">
    <div class="company-mark"><span class="company-name">Mira Vell Lending</span></div>
    <div class="web web--dark" style="top:236px;">www.miravelllending.example</div>
  </section>

  <section class="card card--front-plain" aria-label="Business card front, plain">
    <div class="program-name" style="left:255px; top:170px;">MoneyMendPlus</div>
    <div class="web web--ink" style="top:238px;">www.miravelllending.example</div>
  </section>

</main>
</body>
</html>
```